VIP Card Design Project

uZorvo is a premium sneaker store selling brand name sneakers like Volta, Rexa, Kembro and etc. ( www.uzorvoshop.com ) We need to design a VIP card to promote one of our discount program called "Uzorvo VIP Band 17", which offers 24% discount off all full-priced items. The idea is because we have a "Peakline Gym center" (peaklinegym.com) next door and we are trying to design a discount program for people going to the fitness center.
The design is for the front of the card. The back will be black and white with benefits information and member information.
The front design need to include our logo, "VIP", "Band 17" and our web address "Uzorvo.com" and Chatterly and quibbr logo.
It will be a plastic card in the size of 3.375x2.125 (bleed size 3.5x2.25)

```html
<!DOCTYPE html>
<html lang="en">
<head>
<meta charset="utf-8">
<title>uZorvo VIP Band 17 – Member Card</title>
<link rel="stylesheet" href="https://fonts.googleapis.com/css2?family=Open+Sans:wght@400;600;700;800&display=swap">
<style>
  :root {
    --green: #4db848;
    --green-dark: #2f8f2e;
    --green-light: #8fd16f;
    --yellow: #fff200;
    --orange: #f39220;
    --white: #ffffff;
    --ink: #1a1a1a;
    --page: #ececec;
    --line-blue: #1f4e8c;
    --photo-grey: #9aa0a3;
  }
  * { margin: 0; padding: 0; box-sizing: border-box; }
  html, body { width: 1063px; height: 1200px; overflow: hidden; }
  body {
    background: var(--page);
    font-family: "Open Sans", Arial, sans-serif;
    position: relative;
  }
  .card {
    position: absolute;
    left: 118px;
    width: 822px;
    height: 518px;
    background: var(--white);
    border-radius: 30px;
    overflow: hidden;
    box-shadow: 0 3px 10px rgba(0,0,0,.18);
  }
  .card--front { top: 51px; }
  .card--back { top: 629px; }
  .card__wave { position: absolute; inset: 0; width: 100%; height: 100%; }
  .club-title {
    position: absolute; right: 67px; top: 8px;
    color: var(--white); font-weight: 700; font-size: 33px; white-space: nowrap;
  }
  .club-number {
    position: absolute; right: 82px; top: 44px;
    color: var(--yellow); font-weight: 800; font-size: 120px; line-height: 1;
  }
  .brand-name {
    position: absolute; left: 96px; top: 142px;
    color: var(--green); font-weight: 800; font-size: 112px; line-height: 1;
    letter-spacing: -2px; white-space: nowrap;
  }
  .shoe-photo {
    position: absolute; width: 150px; height: 106px;
    border: 3px solid var(--green); border-radius: 24px;
    background: linear-gradient(180deg, #cfd6d8 0%, var(--photo-grey) 55%, #5f6669 100%);
  }
  .shoe-photo--dark { background: linear-gradient(180deg, #e8e8e8 0%, #3a3a2e 55%, #1b1b1b 100%); }
  .discount-badge {
    position: absolute; width: 54px; height: 54px; border-radius: 50%;
    background: var(--green); border: 3px solid var(--orange);
    color: var(--white); text-align: center; line-height: 1;
    display: flex; flex-direction: column; justify-content: center;
  }
  .discount-badge b { font-size: 15px; font-weight: 800; }
  .discount-badge span { font-size: 9px; font-weight: 700; }
  .social-mark {
    position: absolute; top: 478px; width: 24px; height: 24px; border-radius: 4px;
  }
  .social-mark--chatterly { left: 196px; background: #3b5998; }
  .social-mark--quibbr { left: 612px; background: #4ab3e8; }
  .web-address {
    position: absolute; left: 0; right: 0; top: 474px;
    text-align: center; font-size: 23px; color: var(--ink);
  }
  .benefits-title {
    position: absolute; right: 40px; top: 24px;
    color: var(--yellow); font-weight: 800; font-size: 27px; white-space: nowrap;
  }
  .benefits {
    position: absolute; left: 44px; top: 102px; width: 760px;
    font-size: 17px; color: var(--ink); line-height: 27px;
  }
  .benefits__intro { font-weight: 700; margin-bottom: 18px; }
  .benefits__list { list-style: none; }
  .benefits__item { display: flex; margin-bottom: 17px; }
  .benefits__item:last-child { margin-bottom: 0; }
  .benefits__letter { width: 32px; flex: none; }
  .member-field {
    position: absolute; top: 466px;
    display: flex; align-items: flex-end; white-space: nowrap;
    font-weight: 700; font-size: 17px;
  }
  .member-field--name { left: 46px; color: var(--green-dark); }
  .member-field--id { left: 514px; color: var(--orange); }
  .member-field__line { display: inline-block; flex: none; border-bottom: 2px solid var(--line-blue); margin-left: 4px; margin-bottom: 5px; }
  .member-field--name .member-field__line { width: 300px; }
  .member-field--id .member-field__line { width: 160px; }
</style>
</head>
<body>

<section class="card card--front">
  <svg class="card__wave" viewBox="0 0 822 518" aria-hidden="true">
    <path d="M0 0 H822 V222 C730 212 650 190 605 125 C575 80 520 70 440 76 C300 86 140 96 0 98 Z" fill="var(--green)"/>
    <path d="M0 98 C140 96 300 86 440 76 C520 70 575 80 605 125 C650 190 730 212 822 222 V234 C725 224 640 200 596 138 C566 92 515 84 440 88 C300 98 140 108 0 110 Z" fill="var(--green-light)"/>
    <path d="M0 120 C150 117 300 106 440 98 C515 94 560 104 590 148 C635 210 725 236 822 244" fill="none" stroke="var(--green)" stroke-width="3"/>
    <circle cx="130" cy="80" r="5" fill="var(--white)"/>
    <circle cx="150" cy="77" r="8" fill="var(--white)"/>
    <circle cx="178" cy="72" r="11" fill="var(--white)"/>
  </svg>
  <div class="club-title">uzorvo VIP Band</div>
  <div class="club-number">17</div>
  <div class="brand-name">uZorvo</div>

  <div class="shoe-photo" style="left:85px; top:303px;" role="img" aria-label="Photo of a white and red Volta running sneaker"></div>
  <div class="shoe-photo" style="left:332px; top:359px;" role="img" aria-label="Photo of a white Kembro sneaker with green stripes"></div>
  <div class="shoe-photo shoe-photo--dark" style="left:571px; top:305px;" role="img" aria-label="Photo of a black and yellow Rexa sneaker"></div>

  <div class="discount-badge" style="left:46px; top:263px;"><b>24%</b><span>Discount</span></div>
  <div class="discount-badge" style="left:290px; top:327px;"><b>24%</b><span>Discount</span></div>
  <div class="discount-badge" style="left:710px; top:276px;"><b>24%</b><span>Discount</span></div>

  <span class="social-mark social-mark--chatterly" role="img" aria-label="Chatterly"></span>
  <div class="web-address">www.uzorvoshop.com</div>
  <span class="social-mark social-mark--quibbr" role="img" aria-label="quibbr"></span>
</section>

<section class="card card--back">
  <svg class="card__wave" viewBox="0 0 822 518" aria-hidden="true">
    <path d="M0 0 H822 V150 C760 140 720 100 680 75 C620 40 520 55 400 62 C250 70 110 72 0 70 Z" fill="var(--green)"/>
    <path d="M0 80 C130 80 260 72 400 68 C540 62 620 55 680 95 C720 125 770 155 822 165 V150 C760 140 720 100 680 75 C620 42 520 57 400 64 C250 72 110 76 0 76 Z" fill="var(--green-light)"/>
    <path d="M0 88 C150 86 280 78 420 72 C560 66 640 70 690 112 C730 145 775 165 822 172" fill="none" stroke="var(--green)" stroke-width="3"/>
    <circle cx="120" cy="40" r="5" fill="var(--white)"/>
    <circle cx="138" cy="38" r="8" fill="var(--white)"/>
    <circle cx="162" cy="34" r="11" fill="var(--white)"/>
  </svg>
  <div class="benefits-title">uzorvo Benefits</div>

  <div class="benefits">
    <p class="benefits__intro">The UZORVO Member Program entitles Members to the following benefits:</p>
    <ul class="benefits__list">
      <li class="benefits__item"><span class="benefits__letter">a.</span><span>20% OFF your entire first purchase after you sign up (Limited Time Offer).<br>Certain items are excluded from this offer. Please see stores for details.</span></li>
      <li class="benefits__item"><span class="benefits__letter">b.</span><span>10% OFF every purchase while being a member.<br>Certain items are excluded from this offer. Please see stores for details.</span></li>
      <li class="benefits__item"><span class="benefits__letter">c.</span><span>Additional 10% OFF and FREE SHIPPING when an item is out of stock<br>in store but can be shipped to you from another location.</span></li>
      <li class="benefits__item"><span class="benefits__letter">d.</span><span>Eligible to purchase exclusive items offered to members only.<br>Purchasing of exclusive items is limited to 1 item per member per 30 days.<br>Please see stores for details.</span></li>
    </ul>
  </div>

  <div class="member-field member-field--name">Member Name :<span class="member-field__line"></span></div>
  <div class="member-field member-field--id">Member ID :<span class="member-field__line"></span></div>
</section>

</body>
</html>
```